Etikett für Rotweinflasche
Liebe farbkosmos Atelier, wir werden uns bei der endgültigen Etikettengestaltung (finale Größe + Rückseite) noch an Euch melden. Bitte sendet uns euren Kontakt an helga.brandt@morvelli.wine
Zielgruppe
Morvelli Italia ist ein exklusives Boutique-Weingut in Sizilien, das hochqualitative Spitzenweine in kleinen Mengen mit modernster Technologie und stets nachhaltig erzeugt. Wir hinterfragen sowohl in der Agronomie im Weingarten als auch in der Önologie im Weinkeller alle herrschenden Traditionen und trachten danach, stets das beste Endprodukt zu kreieren. Der vulkanische, kalkreiche Boden Siziliens sowie trockene, sonnenreiche und niederschlagsarme Vegetationsperioden sind unsere optimale Basis.
Zielgruppe: Internationale Genussmenschen jeglichen Alters, die sich bewusst auch höherpreisige Weine (um die €30+) gönnen , vor allem kunstaffine young professionals mit Qualitäts-& Nachhaltigkeitsanspruch
Aufgabenstellung
Das Etikett ist für Rotwein-Flaschen (Cabernet Sauvignon / Nero D'Avola / Frappato / Syrah / Cerasuolo / Petit Verdot / sowie einen Bourdeaux-Cuveè aus Cabernet Sauvignon und Petit Verdot) .
Die Flasche ist reinschwarz, sehr hochwertig und schwer.
Flaschenform: Bordeauxflasche siehe technisches Datenblatt
Sleeve über dem Korken: schwarz mit weißer Schrift wie bisher
Zu gestalten ist das Etikett der Vorderseite. Zumindest die jeweilige Rotwein-Sorte ist auch textlich darzustellen (zwecks Scannen mit Trubel-App)
Der Kreativität kann freien Lauf gelassen werden! Unterscheidbarkeit vom Markt ist explizit gewollt.
Unsere aktuellen Etiketten und Markenauftritt siehe: https://morvelli.wine/shop/

```html
<!DOCTYPE html>
<html lang="de">
<head>
<meta charset="utf-8">
<title>Morvelli Italia – Frappato</title>
<link rel="stylesheet" href="https://fonts.googleapis.com/css2?family=Barlow+Condensed:wght@400;700&family=Poppins:wght@700&family=Barlow:wght@400&display=swap">
<style>
  :root {
    --frame: #767676;
    --label: #ffffff;
    --ink: #0a0a0a;
    --art-light: #e6e6e6;
    --art-dark: #8a8a8a;
  }
  html, body {
    margin: 0;
    padding: 0;
    width: 1200px;
    height: 800px;
    overflow: hidden;
    background: var(--frame);
  }
  .canvas {
    position: relative;
    width: 1200px;
    height: 800px;
    background: var(--frame);
  }
  .label {
    position: absolute;
    left: 38px;
    top: 38px;
    width: 1124px;
    height: 724px;
    background: var(--label);
    color: var(--ink);
  }
  .brand {
    position: absolute;
    left: 30px;
    top: 46px;
    margin: 0;
    font-family: "Barlow Condensed", sans-serif;
    font-weight: 700;
    font-size: 46px;
    letter-spacing: 4px;
    line-height: 1;
    text-transform: uppercase;
  }
  .variety {
    position: absolute;
    left: 28px;
    top: 280px;
    margin: 0;
    font-family: "Poppins", sans-serif;
    font-weight: 700;
    font-size: 118px;
    letter-spacing: -1px;
    line-height: 1;
  }
  .region {
    position: absolute;
    left: 30px;
    top: 548px;
    margin: 0;
    font-family: "Barlow Condensed", sans-serif;
    font-weight: 700;
    font-size: 46px;
    letter-spacing: 4px;
    line-height: 1;
    text-transform: uppercase;
  }
  .vintage {
    position: absolute;
    left: 30px;
    top: 632px;
    margin: 0;
    font-family: "Barlow", sans-serif;
    font-weight: 400;
    font-size: 34px;
    letter-spacing: 2px;
    line-height: 1;
  }
  .artwork {
    position: absolute;
    left: 691px;
    top: 63px;
    width: 392px;
    height: 590px;
  }
</style>
</head>
<body>
<div class="canvas">
  <section class="label">
    <h2 class="brand">Morvelli Italia</h2>
    <h1 class="variety">FRAPPATO</h1>
    <p class="region">Sizilien</p>
    <p class="vintage">2022</p>
    <svg class="artwork" viewBox="0 0 392 590" role="img" aria-label="Schwarzweiß-Zeichnung eines barocken Kircheninnenraums mit verziertem Deckengewölbe und Altar">
      <defs>
        <linearGradient id="artTone" x1="0" y1="0" x2="0" y2="1">
          <stop offset="0" stop-color="var(--art-dark)"/>
          <stop offset="0.55" stop-color="var(--art-light)"/>
          <stop offset="1" stop-color="var(--art-dark)"/>
        </linearGradient>
      </defs>
      <rect width="392" height="590" fill="url(#artTone)"/>
    </svg>
  </section>
</div>
</body>
</html>
```